Private Investigation Business Card Design

I need a business card for a new private investigation company named Brisk Inquiries. I perform mainly surveillance jobs, vehicle repossessions, document serves etc. The final design should aim for a professional look. The logo has a magnifying glass with stick man arms and legs and is in a running action to show the "Brisk" aspect of the name. If the colour scheme could remain the same as the website www.briskinquiries-demo.com.au with silvers,blacks and a couple electric blue highlights.
Industry/Entity Type
Business
Contact Information for Business Card
Morgan Kellaway
Brisk Inquiries
0487316204
PO Box 58, Carnwell NSW 2291
info@briskinquiries-demo.com.au
www.briskinquiries-demo.com.au
Look and feel

```html
<!DOCTYPE html>
<html lang="en">
<head>
<meta charset="utf-8">
<title>Brisk Inquiries – Business Card</title>
<link href="https://fonts.googleapis.com/css2?family=Open+Sans:wght@400;700&display=swap" rel="stylesheet">
<style>
  :root {
    --page-bg: #2a2b2d;
    --silver-light: #c9c9cb;
    --silver-mid: #a9a9ac;
    --silver-dark: #8d8d90;
    --paper: #ffffff;
    --ink: #1d1d1f;
    --ink-soft: #3a3a3c;
    --rule: #4a4a4c;
  }
  * { box-sizing: border-box; margin: 0; padding: 0; }
  html, body {
    width: 1200px; height: 871px; overflow: hidden;
    background: var(--page-bg);
    font-family: "Open Sans", Arial, sans-serif;
  }
  .sheet {
    width: 1200px; height: 871px;
    display: flex; flex-direction: column; align-items: center; justify-content: center;
    gap: 34px;
  }
  .card {
    position: relative; width: 660px; height: 377px; overflow: hidden;
    border-radius: 3px;
    box-shadow: 0 10px 30px rgba(0,0,0,.45);
  }

  /* Back side */
  .card--back {
    background: linear-gradient(160deg, var(--silver-light) 0%, var(--silver-mid) 55%, var(--silver-dark) 100%);
  }
  .card--back .brand { position: absolute; left: 140px; top: 130px; }
  .card--back .brand-name { font-size: 46px; }
  .card--back .web-line {
    position: absolute; left: 170px; top: 232px;
    display: flex; align-items: center; gap: 10px;
    font-size: 15px; letter-spacing: 2px; color: var(--ink-soft);
  }
  .card--back .web-line::after {
    content: ""; width: 70px; height: 1px; background: var(--rule);
  }

  /* Brand block */
  .brand { display: flex; align-items: center; gap: 14px; }
  .brand-name {
    font-weight: 700; color: var(--ink-soft);
    font-size: 34px; line-height: 1; letter-spacing: 1px;
  }
  .brand-dot {
    width: 26px; height: 26px; border-radius: 50%;
    background: var(--silver-mid); border: 2px solid var(--ink-soft);
  }

  /* Front side */
  .card--front { background: var(--paper); }
  .card--front .wave { position: absolute; inset: 0; }
  .card--front .brand { position: absolute; left: 36px; top: 40px; }
  .contact {
    position: absolute; right: 26px; top: 168px;
    text-align: right; color: var(--ink);
  }
  .contact-name { font-weight: 700; font-size: 19px; margin-bottom: 12px; margin-right: 24px; }
  .contact-line {
    display: flex; justify-content: flex-end; align-items: center; gap: 8px;
    font-size: 14px; line-height: 20px; color: var(--ink-soft);
  }
  .contact-line .icon { width: 16px; height: 16px; flex: none; }
  .contact-line .icon--blank { width: 16px; }
</style>
</head>
<body>
<main class="sheet">

  <section class="card card--back" aria-label="Card back">
    <div class="brand">
      <span class="brand-name">Brisk Inquiries</span>
      <span class="brand-dot"></span>
    </div>
    <p class="web-line">www.briskinquiries-demo.com.au</p>
  </section>

  <section class="card card--front" aria-label="Card front">
    <svg class="wave" viewBox="0 0 660 377" preserveAspectRatio="none" aria-hidden="true">
      <defs>
        <linearGradient id="waveFill" x1="0" y1="0" x2="0" y2="1">
          <stop offset="0" stop-color="#b9b9bc"/>
          <stop offset="1" stop-color="#9a9a9d"/>
        </linearGradient>
      </defs>
      <path d="M0 200 C120 330 330 160 660 175 L660 377 L0 377 Z" fill="#dcdcde"/>
      <path d="M0 218 C130 345 340 180 660 192 L660 377 L0 377 Z" fill="url(#waveFill)"/>
      <path d="M0 230 C140 355 350 192 660 204" fill="none" stroke="#eeeeef" stroke-width="2"/>
    </svg>

    <div class="brand">
      <span class="brand-name">Brisk Inquiries</span>
      <span class="brand-dot"></span>
    </div>

    <div class="contact">
      <p class="contact-name">Morgan Kellaway</p>
      <p class="contact-line"><span>PO Box 58</span><span class="icon--blank"></span></p>
      <p class="contact-line"><span>Carnwell NSW 2291</span><span class="icon--blank"></span></p>
      <p class="contact-line">
        <span>0487 316 204</span>
        <svg class="icon" viewBox="0 0 16 16" aria-hidden="true"><path d="M3 4h10l-1 3H4z M4 8h8v5H4z" fill="#1d1d1f"/><circle cx="8" cy="10.5" r="1.3" fill="#fff"/></svg>
      </p>
      <p class="contact-line">
        <span>info@briskinquiries-demo.com.au</span>
        <svg class="icon" viewBox="0 0 16 16" aria-hidden="true"><rect x="1.5" y="4" width="13" height="9" fill="#1d1d1f"/><path d="M1.5 4l6.5 5 6.5-5" fill="none" stroke="#fff" stroke-width="1"/></svg>
      </p>
      <p class="contact-line">
        <span>www.briskinquiries-demo.com.au</span>
        <svg class="icon" viewBox="0 0 16 16" aria-hidden="true"><circle cx="8" cy="8" r="6.5" fill="#1d1d1f"/><path d="M1.5 8h13 M8 1.5c-3 3-3 10 0 13 M8 1.5c3 3 3 10 0 13" fill="none" stroke="#fff" stroke-width=".8"/></svg>
      </p>
    </div>
  </section>

</main>
</body>
</html>
```